Business Card Design

New business card design

Target Market(s)

Residential & Commercial Property Managers

Industry/Entity Type

Plumbing Services

Contact Information for Business Card

Name - Rowan Keddle, title - Director, Phone Number - 0431 286 517, email - rowan@tbk-plumbing.com.au, Company ABN - 73 215 904 386,

Font styles to use
Sans Serif

Colors
0054AA
0677BA
7BADD7
CADEEF
E8F1F8

```html
<!DOCTYPE html>
<html lang="en">
<head>
<meta charset="utf-8">
<title>TBK Plumbing Services – Business Card</title>
<link href="https://fonts.googleapis.com/css2?family=Montserrat:wght@400;500;700&display=swap" rel="stylesheet">
<style>
  :root {
    --ink: #1d232a;
    --ink-faint: #2c353e;
    --accent: #29a3dc;
    --paper: #ffffff;
    --stage: #e9ecef;
  }
  * { box-sizing: border-box; margin: 0; padding: 0; }
  html, body { width: 1200px; height: 912px; overflow: hidden; }
  body {
    background: var(--stage);
    font-family: "Montserrat", Arial, sans-serif;
    position: relative;
  }
  .card {
    position: absolute;
    left: 250px;
    width: 700px;
    height: 400px;
    border-radius: 22px;
    overflow: hidden;
    box-shadow: 0 6px 18px rgba(0,0,0,.18);
  }
  .card--back { top: 36px; background: var(--ink); }
  .card--front { top: 476px; background: var(--paper); }

  .swoosh { position: absolute; left: 0; top: 0; }

  .wordmark {
    position: absolute;
    display: flex;
    align-items: center;
    gap: 10px;
    font-weight: 500;
    white-space: nowrap;
  }
  .wordmark__dot {
    width: 14px; height: 14px;
    border-radius: 50%;
    background: var(--accent);
    flex: none;
  }
  .wordmark__name { letter-spacing: 1px; }
  .card--back .wordmark {
    left: 50%; top: 50%;
    transform: translate(-50%, -50%);
    font-size: 40px;
    color: var(--ink-faint);
    gap: 14px;
  }
  .card--back .wordmark__dot { width: 18px; height: 18px; }
  .card--front .wordmark {
    left: 40px; top: 160px;
    font-size: 21px;
    color: var(--ink);
  }

  .divider {
    position: absolute;
    left: 382px; top: 100px;
    width: 1.5px; height: 150px;
    background: var(--accent);
  }
  .contact {
    position: absolute;
    left: 404px; top: 88px;
    color: var(--ink);
  }
  .contact__name {
    font-size: 28px; font-weight: 700;
    color: var(--accent);
    line-height: 1.1;
  }
  .contact__role { font-size: 18px; margin-top: 2px; }
  .contact__abn { font-size: 16px; margin-top: 14px; }
  .contact__abn-label { color: var(--accent); }
  .contact__line {
    display: flex; align-items: center; gap: 10px;
    font-size: 16px; margin-top: 12px;
  }
  .contact__line + .contact__line { margin-top: 6px; }
  .contact__icon { width: 15px; height: 15px; flex: none; }
</style>
</head>
<body>

  <section class="card card--back" aria-label="Card back">
    <div class="wordmark">
      <span class="wordmark__name">TBK Plumbing Services</span>
      <span class="wordmark__dot"></span>
    </div>
  </section>

  <section class="card card--front" aria-label="Card front">
    <svg class="swoosh" width="700" height="400" viewBox="0 0 700 400" aria-hidden="true">
      <path d="M0 350 Q 420 318 700 292 V400 H0 Z" fill="var(--ink)"/>
      <path d="M330 332 Q 560 310 700 280" fill="none" stroke="var(--accent)" stroke-width="4"/>
    </svg>

    <div class="wordmark">
      <span class="wordmark__name">TBK Plumbing Services</span>
      <span class="wordmark__dot"></span>
    </div>

    <div class="divider"></div>

    <div class="contact">
      <div class="contact__name">Rowan Keddle</div>
      <div class="contact__role">Director</div>
      <div class="contact__abn"><span class="contact__abn-label">ABN</span> - 73 215 904 386</div>
      <div class="contact__line">
        <svg class="contact__icon" viewBox="0 0 16 16" aria-hidden="true">
          <path d="M3.5 1.5l2.5 3-1.5 1.5c.8 2 2.5 3.7 4.5 4.5L10.5 9l3 2.5-1.5 2.5C7 13.5 2.5 9 2 3.5z" fill="var(--accent)"/>
        </svg>
        <span>0431 286 517</span>
      </div>
      <div class="contact__line">
        <svg class="contact__icon" viewBox="0 0 16 16" aria-hidden="true">
          <rect x="1" y="3" width="14" height="10" fill="var(--accent)"/>
          <path d="M1 3l7 6 7-6" fill="none" stroke="#fff" stroke-width="1.3"/>
        </svg>
        <span>rowan@tbk-plumbing.com.au</span>
      </div>
    </div>
  </section>

</body>
</html>
```